New Business Card Design Project

I'd like a business card design around the same modern style that I used on my website www.brovanhs.com
It's gonna be one of those round corners double-sided business cards with maybe a big logo on the front and all the info on the back of the card.

Contact Information for Business Card

Marco Delgado
425-317-6084
www.brovanhs.com

www.facebook.com/BrovanHomeServices
www.intsgram.com/BrovanHomeServices

Requirements
Must have
• it needs to look elegant and modern

```html
<!DOCTYPE html>
<html lang="en">
<head>
<meta charset="utf-8">
<title>Brovan Home Services – Business Card</title>
<link href="https://fonts.googleapis.com/css2?family=Montserrat:wght@400;500;700;800&display=swap" rel="stylesheet">
<style>
  :root{
    --stage:#1f1f24;
    --card-light:#f3f3f3;
    --photo-a:#e9e9ea;
    --photo-b:#d6d6d8;
    --band:#2b2a2c;
    --accent:#1d9be6;
    --white:#ffffff;
  }
  *{margin:0;padding:0;box-sizing:border-box}
  html,body{width:1200px;height:800px;overflow:hidden}
  body{
    background:var(--stage);
    font-family:"Montserrat",Arial,sans-serif;
    display:flex;align-items:center;justify-content:center;gap:50px;
  }
  .card{
    position:relative;width:540px;height:310px;border-radius:22px;overflow:hidden;
    background:var(--card-light);
    box-shadow:0 18px 40px rgba(0,0,0,.45);
  }
  .card__photo{
    position:absolute;inset:0;
    background:linear-gradient(135deg,var(--photo-a) 0%,var(--white) 45%,var(--photo-b) 100%);
    opacity:.9;
  }
  .brand{
    position:absolute;color:var(--accent);font-weight:800;line-height:1;
    text-align:center;white-space:nowrap;letter-spacing:.3px;
  }
  .card--front .brand{left:0;right:0;top:134px;font-size:40px}
  .card--back .brand{left:100px;width:380px;top:40px;font-size:28px}
  .band{position:absolute;inset:0;width:100%;height:100%}
  .contact{position:absolute;left:74px;bottom:26px;color:var(--white)}
  .contact__name{font-weight:700;font-size:19px;margin-bottom:10px}
  .contact__row{display:flex;align-items:center;gap:9px;font-size:13px;margin-top:5px;font-weight:500}
  .icon{width:16px;height:16px;background:var(--accent);border-radius:3px;display:flex;align-items:center;justify-content:center}
  .icon svg{width:11px;height:11px}
  .social{position:absolute;right:26px;top:156px;color:var(--white);font-size:12.5px;font-weight:500}
  .social__row{display:flex;align-items:center;gap:8px;margin-top:5px}
  .social__mark{width:14px;height:14px;background:var(--accent);border-radius:2px}
</style>
</head>
<body>

  <section class="card card--front">
    <div class="card__photo" role="img" aria-label="Faint photo of a bright, clean living room"></div>
    <div class="brand">Brovan Home Services</div>
  </section>

  <section class="card card--back">
    <div class="card__photo" role="img" aria-label="Faint photo of a tidy dining room with flowers"></div>
    <div class="brand">Brovan Home Services</div>

    <svg class="band" viewBox="0 0 540 310" preserveAspectRatio="none" aria-hidden="true">
      <polygon points="0,310 0,282 52,164 212,164 540,58 540,310" fill="var(--white)"/>
      <polygon points="0,310 0,296 58,171 216,171 540,66 540,310" fill="var(--accent)"/>
      <polygon points="10,310 64,178 220,178 540,74 540,310" fill="var(--band)"/>
    </svg>

    <div class="contact">
      <div class="contact__name">Marco Delgado</div>
      <div class="contact__row">
        <span class="icon"><svg viewBox="0 0 24 24"><path fill="#fff" d="M6.6 10.8a15 15 0 0 0 6.6 6.6l2.2-2.2c.3-.3.7-.4 1-.2 1.1.4 2.3.6 3.6.6.6 0 1 .4 1 1V20c0 .6-.4 1-1 1A17 17 0 0 1 3 4c0-.6.4-1 1-1h3.5c.6 0 1 .4 1 1 0 1.3.2 2.5.6 3.6.1.3 0 .7-.2 1z"/></svg></span>
        425-317-6084
      </div>
      <div class="contact__row">
        <span class="icon"><svg viewBox="0 0 24 24" fill="none" stroke="#fff" stroke-width="2"><circle cx="12" cy="12" r="9"/><path d="M3 12h18M12 3c3 3 3 15 0 18M12 3c-3 3-3 15 0 18"/></svg></span>
        www.brovanhs.com
      </div>
    </div>

    <div class="social">
      <div class="social__row"><span class="social__mark"></span>BrovanHomeServices</div>
      <div class="social__row"><span class="social__mark"></span>BrovanHomeServices</div>
    </div>
  </section>

</body>
</html>
```